Marwick Law Letterhead

We need a new letterhead design for a Law Firm. The address for the law firm is 1475 Calloway Street, Suite 210, Houston, Texas 77041. Phone Number: 832-361-9027; Fax Number: 832-614-7359. The logo is uploaded to the project.

```html
<!DOCTYPE html>
<html lang="en">
<head>
<meta charset="utf-8">
<title>Marwick Law Letterhead</title>
<link href="https://fonts.googleapis.com/css2?family=Montserrat:wght@400;500;600&display=swap" rel="stylesheet">
<style>
  :root {
    --backdrop: #e8e8e8;
    --paper: #ffffff;
    --navy: #1c2f5e;
    --navy-light: #22386c;
    --red: #d9202c;
    --maroon: #7a1020;
    --ink: #1a1a1a;
  }
  * { margin: 0; padding: 0; box-sizing: border-box; }
  html, body {
    width: 1154px; height: 1200px; overflow: hidden;
    background: var(--backdrop);
    font-family: "Montserrat", sans-serif;
  }
  .letterhead {
    position: absolute; left: 167px; top: 27px;
    width: 820px; height: 1146px;
    background: var(--paper);
    box-shadow: 0 2px 10px rgba(0,0,0,0.08);
  }
  .brand {
    position: absolute; left: 29px; top: 66px;
    display: flex; align-items: center; gap: 12px;
  }
  .brand-mark {
    width: 40px; height: 40px; background: var(--navy);
  }
  .brand-name {
    font-family: "Montserrat", sans-serif;
    font-weight: 600; font-size: 30px; letter-spacing: 0.5px;
    color: var(--navy);
  }
  .contact {
    position: absolute; left: 613px; top: 62px;
    border-left: 1.5px solid var(--red);
    padding-left: 13px;
    font-size: 14px; line-height: 18px; color: var(--ink);
    height: 96px;
  }
  .contact-address { margin-bottom: 11px; }
  .contact-line { display: flex; align-items: center; gap: 9px; height: 20px; }
  .contact-line svg { width: 13px; height: 13px; flex: none; }
  .header-rule {
    position: absolute; left: 29px; top: 195px;
    width: 761px; height: 2px; background: var(--red);
  }
  .footer-band {
    position: absolute; left: 0; top: 1069px; width: 820px; height: 48px;
  }
  .footer-band svg { display: block; }
  .footer-web {
    position: absolute; left: 490px; top: 0; height: 48px;
    display: flex; align-items: center; gap: 8px;
    color: #fff; font-size: 13.5px; font-weight: 500;
  }
  .footer-web svg { width: 14px; height: 14px; }
</style>
</head>
<body>
  <main class="letterhead">
    <header>
      <div class="brand">
        <span class="brand-mark"></span>
        <span class="brand-name">Marwick Law</span>
      </div>
      <address class="contact" style="font-style:normal">
        <p class="contact-address">1475 Calloway Street,<br>Suite 210, Houston,<br>Texas 77041</p>
        <p class="contact-line">
          <svg viewBox="0 0 24 24" aria-hidden="true"><path fill="#d9202c" d="M6.6 10.8a15.1 15.1 0 0 0 6.6 6.6l2.2-2.2c.3-.3.7-.4 1-.2 1.1.4 2.3.6 3.6.6.6 0 1 .4 1 1V20c0 .6-.4 1-1 1A17 17 0 0 1 3 4c0-.6.4-1 1-1h3.5c.6 0 1 .4 1 1 0 1.3.2 2.5.6 3.6.1.3 0 .7-.2 1z"/></svg>
          832-361-9027
        </p>
        <p class="contact-line">
          <svg viewBox="0 0 24 24" aria-hidden="true"><rect x="6" y="2" width="12" height="6" fill="#d9202c"/><rect x="2" y="9" width="20" height="9" rx="2" fill="#d9202c"/><rect x="6" y="14" width="12" height="8" fill="#fff" stroke="#d9202c" stroke-width="2"/></svg>
          832-614-7359
        </p>
      </address>
      <div class="header-rule"></div>
    </header>

    <footer class="footer-band">
      <svg width="820" height="48" viewBox="0 0 820 48" aria-hidden="true">
        <defs>
          <linearGradient id="navyBand" x1="0" x2="1">
            <stop offset="0" stop-color="#17294f"/>
            <stop offset="1" stop-color="#22386c"/>
          </linearGradient>
          <linearGradient id="redBand" x1="0" x2="1">
            <stop offset="0" stop-color="#d9202c"/>
            <stop offset="0.55" stop-color="#c81d2a"/>
            <stop offset="1" stop-color="#6e0e1b"/>
          </linearGradient>
        </defs>
        <polygon points="0,0 482,0 451,48 0,48" fill="url(#navyBand)"/>
        <polygon points="493,0 684,0 654,48 462,48" fill="url(#redBand)"/>
        <polygon points="696,0 820,0 820,48 665,48" fill="url(#navyBand)"/>
      </svg>
      <div class="footer-web">
        <svg viewBox="0 0 24 24" aria-hidden="true"><circle cx="12" cy="12" r="10" fill="none" stroke="#fff" stroke-width="2"/><ellipse cx="12" cy="12" rx="4" ry="10" fill="none" stroke="#fff" stroke-width="1.6"/><line x1="2" y1="12" x2="22" y2="12" stroke="#fff" stroke-width="1.6"/></svg>
        www.marwicklaw.com
      </div>
    </footer>
  </main>
</body>
</html>
```